Business Card Design

We need a design for business cards for our company. We have a logo. We teach EMT's and we are based out of Virginia. The information that will need to add would be, name, title, phone number, email, address. On the back of the business card would be "We help you, help others"

Target Market(s)

People that want to become EMT's

Colors

Designer to choose colors to be used in the design.

Requirements
Must have
• company logo

```html
<!DOCTYPE html>
<html lang="en">
<head>
<meta charset="UTF-8">
<title>Crestline Medic Academy – Business Cards</title>
<link href="https://fonts.googleapis.com/css2?family=Montserrat:wght@300;600&family=Lato:wght@400;700&family=Libre+Baskerville&display=swap" rel="stylesheet">
<style>
  :root {
    --page: #e6e7ea;
    --card: #1f2a33;
    --red: #ff2747;
    --grey: #7d8a96;
    --pulse-soft: rgba(90, 104, 116, 0.22);
    --white: #ffffff;
  }
  * { margin: 0; padding: 0; box-sizing: border-box; }
  html, body { width: 1200px; height: 900px; overflow: hidden; background: var(--page); }
  .canvas { position: relative; width: 1200px; height: 900px; }
  .card {
    position: absolute; left: 240px; width: 720px; height: 411px;
    background: var(--card); overflow: hidden;
    box-shadow: 0 6px 18px rgba(0,0,0,0.25);
  }
  .card--back { top: 24px; }
  .card--front { top: 465px; }
  .card svg.decor { position: absolute; inset: 0; }
  .pulse-area {
    position: absolute;
    background: linear-gradient(90deg, transparent, var(--pulse-soft) 50%, transparent);
  }
  .card--back .pulse-area { left: 0; right: 0; top: 210px; height: 110px; }
  .card--front .pulse-area { left: 280px; right: 0; top: 130px; height: 100px; }
  .brand {
    position: absolute; display: flex; align-items: center; gap: 12px;
    font-family: "Montserrat", sans-serif; font-weight: 600;
    color: var(--red); letter-spacing: 1px; white-space: nowrap;
  }
  .brand__dot { width: 12px; height: 12px; border-radius: 50%; background: var(--red); }
  .card--back .brand { left: 110px; top: 120px; font-size: 28px; }
  .card--front .brand { left: 150px; top: 92px; font-size: 26px; }
  .tagline {
    position: absolute; left: 0; right: 0; top: 262px; text-align: center;
    font-family: "Libre Baskerville", serif; font-size: 19px;
    color: var(--white); letter-spacing: 0.5px;
  }
  .contact {
    position: absolute; left: 46px; top: 262px;
    font-family: "Lato", sans-serif; color: var(--white);
  }
  .contact__name { font-family: "Montserrat", sans-serif; font-size: 20px; color: var(--red); }
  .contact__name strong { font-weight: 600; }
  .contact__name span { font-weight: 300; }
  .contact__title { font-size: 13px; font-weight: 700; margin-top: 2px; }
  .contact__list { list-style: none; margin-top: 16px; font-size: 13px; }
  .contact__list li { display: flex; align-items: center; gap: 12px; margin-top: 8px; }
  .contact__list svg { width: 14px; height: 14px; fill: var(--red); }
</style>
</head>
<body>
<main class="canvas">

  <section class="card card--back">
    <div class="pulse-area" role="img" aria-label="Faint heartbeat line decoration"></div>
    <div class="brand"><span class="brand__dot"></span>CRESTLINE MEDIC ACADEMY</div>
    <p class="tagline">WE HELP YOU, HELP OTHERS</p>
  </section>

  <section class="card card--front">
    <div class="pulse-area" role="img" aria-label="Faint heartbeat line decoration"></div>
    <svg class="decor" viewBox="0 0 720 411" width="720" height="411" aria-hidden="true">
      <path d="M330,400 Q560,340 720,215" fill="none" stroke="var(--grey)" stroke-width="7"/>
      <path d="M0,411 L0,392 Q430,380 720,232 L720,411 Z" fill="var(--red)"/>
    </svg>
    <div class="brand"><span class="brand__dot"></span>CRESTLINE MEDIC ACADEMY</div>
    <div class="contact">
      <p class="contact__name"><strong>DALIA</strong> <span>VEREEN</span></p>
      <p class="contact__title">Founder / Director</p>
      <ul class="contact__list">
        <li>
          <svg viewBox="0 0 24 24" aria-hidden="true"><path d="M6.6 10.8a15 15 0 0 0 6.6 6.6l2.2-2.2c.3-.3.7-.4 1-.2 1.1.4 2.3.6 3.6.6.6 0 1 .4 1 1V20c0 .6-.4 1-1 1A17 17 0 0 1 3 4c0-.6.4-1 1-1h3.5c.6 0 1 .4 1 1 0 1.3.2 2.5.6 3.6.1.3 0 .7-.2 1z"/></svg>
          +1 555 014 2290
        </li>
        <li>
          <svg viewBox="0 0 24 24" aria-hidden="true"><path d="M2 5h20v14H2z M2 5l10 8 10-8"/></svg>
          info@crestlinemedic.com
        </li>
      </ul>
    </div>
  </section>

</main>
</body>
</html>
```